Business Card Design (NEW FILES)

ATTENTION: New vector files are available. Please update your design to reflect/use the new (better resolution) logo images.

Seeking a unique and professional business card design for a commercial drone photography/videography business. The layout should feature
the logo (attached) and include the following information:
Owen Tarrick
614-502-7738
www.skylarkreelworks.example
NRD Certified Remote Pilot

Owen Tarrick

```html
<!DOCTYPE html>
<html lang="en">
<head>
<meta charset="utf-8">
<title>Skylark Reelworks — Business Card</title>
<link href="https://fonts.googleapis.com/css2?family=Open+Sans:wght@400;600;800&display=swap" rel="stylesheet">
<style>
  :root {
    --stage: #222222;
    --navy: #1b1c4a;
    --navy-deep: #15163d;
    --orange: #ea8a52;
    --orange-soft: #f09a62;
    --white: #ffffff;
  }
  * { box-sizing: border-box; margin: 0; padding: 0; }
  html, body { width: 1200px; height: 780px; overflow: hidden; }
  body {
    background: var(--stage);
    font-family: "Open Sans", Arial, sans-serif;
    position: relative;
  }
  .card {
    position: absolute;
    width: 540px;
    height: 309px;
    border-radius: 3px;
    overflow: hidden;
    box-shadow: 0 14px 30px rgba(0,0,0,0.55);
  }
  /* Back side */
  .card-back {
    left: 70px;
    top: 70px;
    background: var(--orange);
  }
  .card-back .pattern-area {
    position: absolute;
    inset: 0;
    background: linear-gradient(135deg, var(--orange-soft), var(--orange));
  }
  .card-back .brand-mark {
    position: absolute;
    right: 52px;
    bottom: 40px;
    display: flex;
    align-items: center;
    gap: 7px;
    color: var(--navy);
    font-weight: 600;
    font-size: 15px;
    letter-spacing: 0.5px;
  }
  .brand-dot {
    width: 10px; height: 10px; border-radius: 50%;
    background: currentColor;
  }
  /* Front side */
  .card-front {
    left: 590px;
    top: 400px;
    background: var(--navy);
    color: var(--white);
  }
  .card-front .brand-mark {
    position: absolute;
    left: 32px;
    top: 52px;
    display: flex;
    align-items: center;
    gap: 9px;
    font-weight: 600;
    font-size: 22px;
    letter-spacing: 0.6px;
    color: var(--white);
  }
  .holder {
    position: absolute;
    right: 34px;
    top: 24px;
    text-align: right;
  }
  .holder-name {
    color: var(--orange);
    font-weight: 800;
    font-size: 25px;
    line-height: 1.1;
  }
  .holder-role {
    font-size: 11px;
    margin-top: 2px;
  }
  .accent-bar {
    position: absolute;
    right: 14px;
    top: 20px;
    width: 11px;
    height: 46px;
    background: var(--orange);
  }
  .drone-art {
    position: absolute;
    right: 14px;
    bottom: 42px;
    width: 230px;
    height: 130px;
    border-radius: 60px 60px 80px 40px;
    background: radial-gradient(ellipse at 60% 40%, #2a2b63 0%, var(--navy-deep) 70%, var(--navy) 100%);
  }
  .credentials {
    position: absolute;
    left: 40px;
    bottom: 98px;
    font-size: 12.5px;
    line-height: 1.45;
  }
  .contact-list {
    position: absolute;
    left: 40px;
    bottom: 26px;
    list-style: none;
    font-size: 12.5px;
    line-height: 1.55;
  }
  .contact-list li { display: flex; align-items: center; gap: 8px; }
  .contact-icon { width: 12px; height: 12px; flex: none; }
</style>
</head>
<body>

  <section class="card card-back" aria-label="Card back">
    <div class="pattern-area" role="img" aria-label="Embossed repeating pattern of small camera drones"></div>
    <div class="brand-mark"><span class="brand-dot"></span>Skylark Reelworks</div>
  </section>

  <section class="card card-front" aria-label="Card front">
    <div class="brand-mark"><span class="brand-dot"></span>Skylark Reelworks</div>

    <div class="accent-bar"></div>
    <div class="holder">
      <p class="holder-name">Owen Tarrick</p>
      <p class="holder-role">Owner</p>
    </div>

    <div class="drone-art" role="img" aria-label="Debossed illustration of a camera drone with orange propeller accents"></div>

    <div class="credentials">
      <p>NRD Certified Remote Pilot</p>
      <p>Fully Insured</p>
    </div>

    <ul class="contact-list">
      <li>
        <svg class="contact-icon" viewBox="0 0 24 24" aria-hidden="true"><path fill="#ea8a52" d="M6.6 10.8a15.1 15.1 0 0 0 6.6 6.6l2.2-2.2a1 1 0 0 1 1-.25 11.4 11.4 0 0 0 3.6.57 1 1 0 0 1 1 1V20a1 1 0 0 1-1 1A17 17 0 0 1 3 4a1 1 0 0 1 1-1h3.5a1 1 0 0 1 1 1c0 1.25.2 2.45.57 3.57a1 1 0 0 1-.25 1z"/></svg>
        614-502-7738
      </li>
      <li>
        <svg class="contact-icon" viewBox="0 0 24 24" aria-hidden="true"><circle cx="12" cy="12" r="10" fill="none" stroke="#ea8a52" stroke-width="2"/><path d="M2 12h20M12 2c3 3 3 17 0 20M12 2c-3 3-3 17 0 20" fill="none" stroke="#ea8a52" stroke-width="1.6"/></svg>
        www.skylarkreelworks.example
      </li>
      <li>
        <svg class="contact-icon" viewBox="0 0 24 24" aria-hidden="true"><rect x="2" y="5" width="20" height="14" rx="1.5" fill="none" stroke="#ea8a52" stroke-width="2"/><path d="M2 6l10 7 10-7" fill="none" stroke="#ea8a52" stroke-width="2"/></svg>
        info@skylarkreelworks.example
      </li>
    </ul>
  </section>

</body>
</html>
```